Business Card Design

Velora Pixel Outreach

An online marketing consulting & strategy business for the cosmetic niche

We specialise in Increasing Leads, Conversions & Content Marketing

I am looking for a very clean, BOLD business card that is simple & effective

Target Market(s)

cosmetic surgeons & cosmetic clinics

Industry/Entity Type

Marketing

Contact Information for Business Card

Dermot Kalway
Online Marketing Strategist

Dermot@VeloraPixelOutreach.example
0492 158 620

LinkedIn: in/dermotkalway

```html
<!DOCTYPE html>
<html lang="en">
<head>
<meta charset="utf-8">
<title>Velora Pixel Outreach – Business Card</title>
<link rel="stylesheet" href="https://fonts.googleapis.com/css2?family=Michroma&family=Open+Sans:wght@400;600;700&display=swap">
<style>
  :root {
    --bg: #d6d6d6;
    --card: #ffffff;
    --brand-blue: #29a8e0;
    --brand-green: #9bc93c;
    --ink-grey: #5e5f61;
    --ink-dark: #4a4a4a;
  }
  * { margin: 0; padding: 0; box-sizing: border-box; }
  html, body {
    width: 1200px; height: 985px; overflow: hidden;
    background: var(--bg);
  }
  .stage { position: relative; width: 1200px; height: 985px; }

  .card {
    position: absolute; left: 280px; width: 640px; height: 366px;
    background: var(--card); border-radius: 22px; overflow: hidden;
    box-shadow: 0 6px 18px rgba(0,0,0,.18);
  }
  .card--front { top: 90px; }
  .card--back { top: 530px; }

  .wordmark {
    font-family: "Michroma", sans-serif; color: var(--ink-grey);
    text-transform: uppercase; line-height: 1.05;
  }

  /* Front */
  .front-mark {
    position: absolute; left: 50%; top: 46px; transform: translateX(-50%);
    display: flex; flex-direction: column; align-items: center;
  }
  .front-mark__square {
    width: 96px; height: 86px; border: 2px solid var(--brand-blue); margin-bottom: 14px;
  }
  .front-mark .wordmark { font-size: 27px; letter-spacing: 4px; text-align: left; }
  .front-band {
    position: absolute; left: 0; right: 0; top: 262px; height: 30px;
  }

  /* Back */
  .side-column {
    position: absolute; left: 0; top: 0; width: 150px; height: 100%;
    background: linear-gradient(to bottom, var(--brand-blue), var(--brand-green) 75%);
  }
  .rule-green { position: absolute; left: 160px; top: 0; width: 2px; height: 100%; background: var(--brand-green); }
  .rule-blue { position: absolute; left: 166px; top: 0; width: 1px; height: 100%; background: var(--brand-blue); }
  .logo-box {
    position: absolute; left: 100px; top: 24px; width: 112px; height: 108px;
    background: var(--card); display: flex; align-items: center; justify-content: center;
  }
  .logo-box__square { width: 70px; height: 64px; border: 2px solid var(--brand-blue); }
  .back-wordmark { position: absolute; left: 228px; top: 38px; font-size: 31px; letter-spacing: 5px; }

  .person { position: absolute; left: 190px; top: 178px; }
  .person__name {
    font-family: "Open Sans", sans-serif; font-weight: 700; font-size: 23px; color: var(--brand-blue);
  }
  .person__title {
    font-family: "Open Sans", sans-serif; font-weight: 600; font-size: 15px; color: var(--brand-green);
    padding-bottom: 6px; border-bottom: 1px solid var(--brand-green); width: 300px;
  }
  .contacts { list-style: none; margin-top: 14px; }
  .contacts li {
    display: flex; align-items: center; gap: 12px; margin-bottom: 10px;
    font-family: "Open Sans", sans-serif; font-size: 15px; color: var(--ink-dark);
  }
  .contacts svg { width: 20px; height: 20px; flex: none; }
</style>
</head>
<body>
<main class="stage">

  <section class="card card--front" aria-label="Card front">
    <div class="front-mark">
      <div class="front-mark__square"></div>
      <div class="wordmark">Velora<br>Pixel<br>Outreach</div>
    </div>
    <svg class="front-band" viewBox="0 0 640 30" preserveAspectRatio="none">
      <polygon points="44,30 62,0 72,0 54,30" fill="var(--brand-green)"/>
      <rect x="80" y="0" width="560" height="30" fill="var(--brand-blue)"/>
      <polygon points="0,30 22,0 76,0 54,30" fill="var(--brand-blue)"/>
    </svg>
  </section>

  <section class="card card--back" aria-label="Card back">
    <div class="side-column"></div>
    <div class="rule-green"></div>
    <div class="rule-blue"></div>
    <div class="logo-box"><div class="logo-box__square"></div></div>
    <div class="wordmark back-wordmark">Velora<br>Pixel<br>Outreach</div>

    <div class="person">
      <p class="person__name">Dermot Kalway</p>
      <p class="person__title">Online Marketing Strategist</p>
      <ul class="contacts">
        <li>
          <svg viewBox="0 0 20 20" aria-hidden="true"><rect width="20" height="20" rx="2" fill="var(--brand-blue)"/><path d="M6.5 4.5l2 .3.7 2.6-1.3 1a7 7 0 0 0 3.7 3.7l1-1.3 2.6.7.3 2c-.2.6-.8 1-1.5 1A10 10 0 0 1 5.5 6c0-.7.4-1.3 1-1.5z" fill="#fff"/></svg>
          0492 158 620
        </li>
        <li>
          <svg viewBox="0 0 20 20" aria-hidden="true"><rect width="20" height="20" rx="2" fill="var(--brand-blue)"/><rect x="4" y="6" width="12" height="8.5" fill="none" stroke="#fff" stroke-width="1.3"/><path d="M4 6l6 5 6-5" fill="none" stroke="#fff" stroke-width="1.3"/></svg>
          Dermot@VeloraPixelOutreach.example
        </li>
        <li>
          <svg viewBox="0 0 20 20" aria-hidden="true"><rect width="20" height="20" rx="2" fill="var(--brand-blue)"/></svg>
          in/dermotkalway
        </li>
      </ul>
    </div>
  </section>

</main>
</body>
</html>
```